Brivolt Technologies business card design

We need a business card designed with our new logo. it would be great if the card could communicate it is a technology based company.

Target Market(s)

system integrators

Industry/Entity Type

technology, IOT

Contact Information for Business Card

Name, designation, Address, telephone number, email address

Requirements
Must have
• logo and company name
Nice to have
• something to do with technology

```html
<!DOCTYPE html>
<html lang="en">
<head>
<meta charset="utf-8">
<title>Brivolt Technologies – Business Card</title>
<link href="https://fonts.googleapis.com/css2?family=Inter:wght@400;600&display=swap" rel="stylesheet">
<style>
  :root {
    --backdrop: #1c1c1d;
    --card: #3a3a3c;
    --card-deep: #2e2e30;
    --pattern-light: #4a4a4d;
    --orange: #f7931e;
    --white: #ffffff;
    --muted: #e9e9ea;
  }
  * { box-sizing: border-box; margin: 0; padding: 0; }
  html, body {
    width: 1200px; height: 900px; overflow: hidden;
    background: var(--backdrop);
    font-family: "Inter", Arial, sans-serif;
  }
  .stage {
    width: 1200px; height: 900px;
    display: flex; flex-direction: column; align-items: center; justify-content: center;
    gap: 40px;
  }
  .card {
    position: relative;
    width: 630px; height: 360px;
    border-radius: 18px;
    background: var(--card);
    border-bottom: 3px solid var(--orange);
    overflow: hidden;
  }

  /* Front */
  .brand {
    position: absolute; left: 44px; top: 40px;
    display: flex; align-items: center; gap: 12px;
  }
  .brand-square { width: 18px; height: 18px; background: var(--orange); }
  .brand-name {
    color: var(--white); font-weight: 600; font-size: 26px; letter-spacing: 1px;
    text-transform: uppercase;
  }
  .divider {
    position: absolute; left: 60px; right: 90px; top: 205px;
    height: 1.5px; background: var(--orange);
  }
  .edge-tab {
    position: absolute; right: 0; top: 186px;
    width: 8px; height: 38px; background: var(--orange);
  }
  .person {
    position: absolute; right: 90px; top: 132px; text-align: right;
  }
  .person-name {
    color: var(--orange); font-weight: 600; font-size: 24px; text-transform: uppercase;
    letter-spacing: 0.5px;
  }
  .person-title {
    color: var(--muted); font-size: 15px; text-transform: uppercase; margin-top: 4px;
  }
  .contacts {
    position: absolute; left: 40px; top: 236px; list-style: none;
    display: flex; flex-direction: column; gap: 8px;
  }
  .contacts li {
    display: flex; align-items: center; gap: 10px;
    color: var(--muted); font-size: 15px;
  }
  .contacts svg { width: 14px; height: 14px; flex: none; }
  .address {
    position: absolute; right: 90px; top: 236px; text-align: right;
    color: var(--muted); font-size: 15px; line-height: 1.6; font-style: normal;
  }

  /* Back */
  .card-back { background: var(--card-deep); }
  .back-pattern {
    position: absolute; inset: 0;
    background: linear-gradient(135deg, var(--pattern-light) 0%, var(--card-deep) 55%, #222224 100%);
  }
  .back-brand {
    position: absolute; right: 40px; bottom: 34px;
    display: flex; align-items: center; gap: 10px;
  }
  .back-brand .brand-square { width: 14px; height: 14px; }
  .back-brand .brand-name { font-size: 20px; }
</style>
</head>
<body>
<main class="stage">

  <section class="card card-front">
    <div class="brand">
      <span class="brand-square"></span>
      <span class="brand-name">Brivolt Technologies</span>
    </div>

    <div class="person">
      <p class="person-name">Daniel Brenner</p>
      <p class="person-title">Director</p>
    </div>

    <div class="divider"></div>
    <div class="edge-tab"></div>

    <ul class="contacts">
      <li>
        <svg viewBox="0 0 24 24" fill="none" stroke="var(--orange)" stroke-width="2"><path d="M5 3h4l2 5-3 2a12 12 0 0 0 6 6l2-3 5 2v4a2 2 0 0 1-2 2A17 17 0 0 1 3 5a2 2 0 0 1 2-2z"/></svg>
        (555) 318-4072
      </li>
      <li>
        <svg viewBox="0 0 24 24" fill="none" stroke="var(--orange)" stroke-width="2"><rect x="3" y="5" width="18" height="14" rx="1"/><path d="M3 6l9 7 9-7"/></svg>
        info@brivolttech.com
      </li>
      <li>
        <svg viewBox="0 0 24 24" fill="none" stroke="var(--orange)" stroke-width="2"><circle cx="12" cy="12" r="9"/><path d="M3 12h18M12 3c3 3 3 15 0 18M12 3c-3 3-3 15 0 18"/></svg>
        brivolttech.com
      </li>
    </ul>

    <address class="address">
      1420 Harbor Lane<br>
      Fairview, MI 48000
    </address>
  </section>

  <section class="card card-back">
    <div class="back-pattern" role="img" aria-label="Tone-on-tone repeating brand monogram pattern covering the card back"></div>
    <div class="back-brand">
      <span class="brand-square"></span>
      <span class="brand-name">Brivolt</span>
    </div>
  </section>

</main>
</body>
</html>
```